Calm Harbor Bodywork business is seeking a Business Card Design

We are a new natural therapy business that needs a Business Card Design with an appointment card on the back.

We offer Myotherapy (muscle therapy) services and have a strong focus and commitment to helping people relieve pain and restore movement to their bodies.

I am attaching my business logo for you information.

Business card must contain my logo and have space for name, title, qualifications, phone number, email, web address

Appointment Card on the back of the card must contain space to write next appointment date, time and name of therapist and cancellation policy.

Cancellation Policy
Minimum of 24hrs notice is required prior to appointment time or full treatment fees with apply.

```html
<!DOCTYPE html>
<html lang="en">
<head>
<meta charset="UTF-8">
<title>Calm Harbor Bodywork – Business and Appointment Card</title>
<link href="https://fonts.googleapis.com/css2?family=Lato:wght@400;700;900&display=swap" rel="stylesheet">
<style>
  :root {
    --page-bg: #e9e9e9;
    --card-bg: #ffffff;
    --accent-red: #c11d2c;
    --box-red: #d9545f;
    --brown: #5a463c;
    --green: #72b133;
    --ink: #333333;
    --ink-soft: #4a4a4a;
    --dots: #555555;
  }
  * { box-sizing: border-box; margin: 0; padding: 0; }
  html, body {
    width: 1200px; height: 900px; overflow: hidden;
    background: var(--page-bg);
    font-family: "Lato", Arial, sans-serif;
    color: var(--ink);
  }
  .card {
    position: absolute; left: 250px;
    width: 700px; height: 400px;
    background: var(--card-bg);
    border-radius: 20px;
    box-shadow: 0 8px 24px rgba(0,0,0,0.18);
    overflow: hidden;
  }

  /* ---------- Appointment side ---------- */
  .appointment-card { top: 30px; padding: 38px 56px 0; }
  .label {
    display: block; width: max-content; margin: 0 auto;
    background: var(--accent-red); color: #fff;
    font-weight: 900; letter-spacing: 0.7px;
    text-transform: uppercase; line-height: 1;
  }
  .label--title { font-size: 21px; padding: 5px 9px; }
  .label--policy { font-size: 18px; padding: 5px 9px; }
  .field-row {
    display: flex; align-items: flex-end; gap: 7px;
    font-size: 16px; letter-spacing: 0.7px; color: var(--ink-soft);
    margin-top: 30px;
  }
  .field-label { white-space: nowrap; }
  .field-line {
    flex: 1; border-bottom: 2px dotted var(--dots);
    margin-bottom: 4px; min-width: 30px;
  }
  .field-line--date { flex: 1.1; }
  .period { display: flex; align-items: center; gap: 6px; font-size: 15px; margin-left: 10px; }
  .period + .period { margin-left: 12px; }
  .check {
    display: inline-block; width: 21px; height: 21px;
    border: 2px solid var(--box-red); border-radius: 4px; background: #fff;
  }
  .days { display: flex; justify-content: space-between; margin: 28px 14px 0; }
  .day { display: flex; align-items: center; gap: 7px; font-size: 20px; font-weight: 900; color: var(--ink); }
  .day .check { width: 24px; height: 24px; }
  .field-row--therapist { margin-top: 30px; }
  .policy { margin-top: 30px; text-align: center; }
  .policy-text {
    margin-top: 12px; font-size: 16px; line-height: 1.35;
    color: var(--ink-soft);
  }

  /* ---------- Business side ---------- */
  .business-card { top: 470px; }
  .top-bands { display: flex; height: 16px; }
  .top-bands span { flex: 1; }
  .band--red { background: var(--accent-red); }
  .band--brown { background: var(--brown); }
  .band--green { background: var(--green); }
  .business-body { display: flex; padding: 40px 40px 0; gap: 36px; }
  .brand { width: 330px; }
  .tiles { display: flex; gap: 10px; }
  .tile { width: 100px; height: 100px; }
  .tile--red { background: var(--accent-red); }
  .tile--brown { background: var(--brown); }
  .tile--green { background: var(--green); }
  .brand-name {
    margin-top: 18px; font-size: 25px; font-weight: 900;
    color: var(--accent-red); text-transform: uppercase; line-height: 1.1;
  }
  .brand-tag { margin-top: 6px; font-size: 13px; color: var(--ink-soft); letter-spacing: 0.5px; }
  .person { padding-top: 6px; flex: 1; }
  .person-name { font-size: 24px; font-weight: 900; color: var(--green); text-transform: uppercase; letter-spacing: 0.5px; }
  .person-title { font-size: 15px; font-weight: 900; color: var(--ink); text-transform: uppercase; letter-spacing: 1px; margin-top: 3px; }
  .person-quals { font-size: 13px; color: var(--ink-soft); margin-top: 6px; }
  .contacts { list-style: none; margin-top: 24px; }
  .contacts li { display: flex; align-items: center; gap: 10px; font-size: 14px; color: var(--ink-soft); margin-bottom: 10px; }
  .contacts svg { width: 22px; height: 22px; flex: none; }
  .bottom-band { position: absolute; left: 0; right: 0; bottom: 0; height: 10px; background: var(--brown); }
</style>
</head>
<body>
  <section class="card appointment-card" aria-label="Appointment card">
    <h1 class="label label--title">Next Appointment</h1>
    <div class="field-row">
      <span class="field-label">DATE:</span>
      <span class="field-line field-line--date"></span>
      <span class="field-label">TIME:</span>
      <span class="field-line"></span>
      <span class="period">AM <span class="check"></span></span>
      <span class="period">PM <span class="check"></span></span>
    </div>
    <div class="days">
      <span class="day">Mon <span class="check"></span></span>
      <span class="day">Tue <span class="check"></span></span>
      <span class="day">Wed <span class="check"></span></span>
      <span class="day">Thu <span class="check"></span></span>
      <span class="day">Fri <span class="check"></span></span>
    </div>
    <div class="field-row field-row--therapist">
      <span class="field-label">NAME OF THERAPIST:</span>
      <span class="field-line"></span>
    </div>
    <div class="policy">
      <h2 class="label label--policy">Cancellation Policy</h2>
      <p class="policy-text">Minimum of 24hrs notice is required prior to appointment time or full<br>treatment fees with apply</p>
    </div>
  </section>

  <section class="card business-card" aria-label="Business card">
    <div class="top-bands"><span class="band--red"></span><span class="band--brown"></span><span class="band--green"></span></div>
    <div class="business-body">
      <div class="brand">
        <div class="tiles">
          <div class="tile tile--red" role="img" aria-label="Tile with body outline illustration"></div>
          <div class="tile tile--brown" role="img" aria-label="Tile with muscle line illustration"></div>
          <div class="tile tile--green" role="img" aria-label="Tile with neck and shoulders illustration"></div>
        </div>
        <p class="brand-name">Calm Harbor Bodywork</p>
        <p class="brand-tag">Myotherapy &amp; Muscle Therapy</p>
      </div>
      <div class="person">
        <p class="person-name">Your Name</p>
        <p class="person-title">Designation</p>
        <p class="person-quals">B.Hlth Sc (Myotherapy)</p>
        <ul class="contacts">
          <li><svg viewBox="0 0 24 24"><circle cx="12" cy="12" r="12" fill="#72b133"/><path d="M8 6h3l1 3-2 1a7 7 0 0 0 4 4l1-2 3 1v3a1 1 0 0 1-1 1A11 11 0 0 1 7 7a1 1 0 0 1 1-1z" fill="#fff"/></svg>0400 123 456</li>
          <li><svg viewBox="0 0 24 24"><circle cx="12" cy="12" r="12" fill="#72b133"/><rect x="6" y="8" width="12" height="8" fill="none" stroke="#fff" stroke-width="1.6"/><path d="M6 8l6 5 6-5" fill="none" stroke="#fff" stroke-width="1.6"/></svg>hello@calmharbor.example</li>
          <li><svg viewBox="0 0 24 24"><circle cx="12" cy="12" r="12" fill="#72b133"/><circle cx="12" cy="12" r="6" fill="none" stroke="#fff" stroke-width="1.5"/><path d="M6 12h12M12 6c-3 3-3 9 0 12M12 6c3 3 3 9 0 12" fill="none" stroke="#fff" stroke-width="1.3"/></svg>www.calmharbor.example</li>
        </ul>
      </div>
    </div>
    <div class="bottom-band"></div>
  </section>
</body>
</html>
```